Computers & Components Website

We require a web design for our new look website. We are based in New Zealand. We are an online based business selling computer hardware and software to the NZ market.
The new website should use similar colour scheme to our current site (www.qvz.co.nz).
It needs to be uncluttered and simple to navigate.

Target Market(s)

anyone looking for computer hardware & software etc. Geeks !!

Industry/Entity Type

Business

```html
<!DOCTYPE html>
<html lang="en">
<head>
<meta charset="utf-8">
<title>Quartz PCs – Computer Systems and Components</title>
<link rel="stylesheet" href="https://fonts.googleapis.com/css2?family=Source+Sans+3:wght@400;600;700&display=swap">
<style>
:root{
  --blue:#6b83c2;
  --blue-dark:#3b5a9e;
  --blue-text:#4d67ad;
  --blue-line:#8c9fd1;
  --ink:#333;
  --muted:#666;
  --panel:#f2f2f4;
  --foot:#333;
  --foot-head:#3e3e3e;
  --foot-text:#bbb;
}
*{box-sizing:border-box;margin:0;padding:0}
html,body{width:969px;height:1200px;overflow:hidden;background:#fff}
body{font-family:"Source Sans 3",Arial,sans-serif;color:var(--ink);position:relative}
.abs{position:absolute}
a{color:inherit;text-decoration:none}

/* header */
.brand{left:42px;top:30px;width:150px;height:100px;display:flex;align-items:center;gap:8px}
.brand-dot{width:22px;height:22px;border-radius:50%;background:var(--blue)}
.brand-name{font-size:20px;font-weight:700;color:var(--blue-dark)}
.topbar{left:392px;top:32px;display:flex;align-items:center;gap:10px;font-size:13px}
.topbar .cart{color:var(--blue-dark);font-weight:600}
.topbar .count{color:var(--blue-text)}
.topbar .sep{color:#999}
.topbar .login{color:var(--blue-dark)}
.checkout-btn{background:linear-gradient(#8fa3d8,#6880c0);color:#fff;font-size:11px;padding:3px 10px;border-radius:2px}
.search{left:755px;top:30px;width:175px;height:22px;border:1px solid #ccc;box-shadow:inset 0 1px 2px #ddd;font-size:10px;font-style:italic;color:#999;padding:4px 10px}
.nav{left:198px;top:81px;width:732px;height:40px;background:var(--blue);display:flex}
.nav a{color:#fff;font-size:13px;display:flex;align-items:center;justify-content:center;border-right:1px solid #5a70ad;border-left:1px solid #7b92ce}
.nav a:first-child{border-left:0}
.nav a:last-child{border-right:0}

/* hero */
.hero{left:42px;top:148px;width:886px;height:281px;background:linear-gradient(#eef0f3,#f8f8fa 60%,#f0f1f4);border-bottom:2px solid #e6e7ea}
.hero-inner{left:8px;top:8px;width:870px;height:264px;background:#fff;border:1px solid #eceef1;background:linear-gradient(90deg,#f7f8fa,#fff 30%,#f3f4f7)}
.hero-image{left:48px;top:25px;width:270px;height:222px;background:linear-gradient(160deg,#3a3d44,#16181c 55%,#4a4d53);border-radius:4px}
.hero-tag{left:336px;top:80px;font-size:17px;color:#333}
.hero-title{left:336px;top:104px;font-size:29px;color:var(--blue-text)}
.hero-rule{top:198px;height:1px;background:#d5d7dc}
.hero-dots{left:474px;top:192px;display:flex;gap:19px}
.hero-dots span{width:12px;height:12px;border-radius:50%;background:#8c8f96}
.hero-dots span.on{background:var(--blue)}

/* welcome */
.welcome{left:60px;top:453px;width:624px}
.welcome h1{font-size:21px;font-weight:400;color:#222;padding-bottom:8px;border-bottom:2px dotted #999}
.welcome h1 span{color:var(--blue-text)}
.welcome p{font-size:11.3px;line-height:20.3px;color:#555;text-align:justify;margin-top:10px}

/* product panels */
.panel{left:58px;width:629px;height:193px;background:var(--panel)}
.panel-head{position:absolute;left:14px;right:14px;top:10px;height:32px;border-bottom:1px solid #dadbe0;display:flex;justify-content:space-between;align-items:center}
.panel-head h2{font-size:16.5px;font-weight:400;color:var(--blue-text)}
.panel-head a{font-size:10.5px;color:#333}
.products{position:absolute;left:14px;top:54px;display:flex;gap:33px}
.product{width:96px;text-align:center}
.product-img{width:64px;height:48px;margin:0 auto;border-radius:4px}
.price{font-size:17px;color:var(--blue-dark);margin-top:10px}
.warranty{font-size:10.5px;color:#666;margin-top:1px}
.add-btn{margin-top:7px;height:23px;background:linear-gradient(#4a6aae,#2f4c8d);color:#fff;font-size:10px;font-weight:600;display:flex;align-items:center;justify-content:center;gap:5px;border-radius:2px}

/* category sidebar */
.cats{left:701px;top:459px;width:222px;height:557px;background:var(--blue);padding:6px 0}
.cats li{list-style:none;height:25.85px;border-bottom:1px solid var(--blue-line);margin:0 2px;display:flex;align-items:center;font-size:12.3px;color:#fff}
.cats li:last-child{border-bottom:0}
.cats li::before{content:"";border-left:4px solid #dfe5f5;border-top:3.5px solid transparent;border-bottom:3.5px solid transparent;margin:0 20px 0 35px}

/* footer */
.footer{left:46px;top:1029px;width:874px;height:155px;background:var(--foot);color:var(--foot-text)}
.foot-head{position:absolute;top:0;height:32px;background:var(--foot-head);display:flex;align-items:center;color:#eee}
.foot-col-line{position:absolute;top:0;width:1px;height:155px;background:#555}
.mail-input{left:19px;top:47px;width:193px;height:23px;background:#fff;font-size:10px;font-style:italic;color:#999;padding:5px 12px}
.submit{left:154px;top:81px;height:21px;padding:0 10px;background:linear-gradient(#5a78b9,#3b5a9e);color:#fff;font-size:11px;display:flex;align-items:center}
.nz-fern{left:65px;top:88px;width:42px;height:26px;background:linear-gradient(90deg,#555,#888);border-radius:50%}
.nz-text{left:30px;top:113px;width:115px;text-align:center;font-size:12.5px;font-weight:700;color:#ddd;line-height:15px}
.links{font-size:10.5px;line-height:18.5px;color:#aaa}
.copyright{font-size:10.5px}
.pay-row,.social-row{display:flex;align-items:center;gap:6px;font-size:10.5px}
.pay{background:#f2f2f2;color:#2d4a8c;font-size:8px;font-weight:700;padding:5px 3px;border-radius:2px}
.social{display:flex;align-items:center;gap:3px;color:#ddd;font-size:9.5px}
.social i{width:12px;height:12px;border-radius:50%;background:#fff;display:block}
</style>
</head>
<body>

<header>
  <div class="abs brand"><span class="brand-dot"></span><span class="brand-name">Quartz PCs</span></div>

  <div class="abs topbar">
    <svg width="16" height="13" viewBox="0 0 16 13" aria-hidden="true"><path d="M0 1h3l2 8h8l2-6H4" fill="none" stroke="#444" stroke-width="1.4"/><circle cx="6" cy="11.5" r="1.2" fill="#444"/><circle cx="12" cy="11.5" r="1.2" fill="#444"/></svg>
    <a class="cart" href="#">Shopping Cart</a><span class="count">( 0 ) Items</span>
    <span class="sep">|</span>
    <svg width="15" height="13" viewBox="0 0 15 13" aria-hidden="true"><circle cx="7.5" cy="4" r="3.3" fill="#555"/><path d="M1 13c0-4 3-5.5 6.5-5.5S14 9 14 13z" fill="#555"/></svg>
    <a class="login" href="#">Log In</a>
    <a class="checkout-btn" href="#">Check Out</a>
  </div>
  <div class="abs search">Search Product</div>

  <nav class="abs nav">
    <a href="#" style="width:81px">Home</a>
    <a href="#" style="width:90px">About Us</a>
    <a href="#" style="width:80px">Specials</a>
    <a href="#" style="width:101px">Whats New</a>
    <a href="#" style="width:111px">Stock to Clear</a>
    <a href="#" style="width:93px">PC Wizard</a>
    <a href="#" style="width:89px">Checkout</a>
    <a href="#" style="width:87px">Contact</a>
  </nav>
</header>

<section class="abs hero">
  <div class="abs hero-inner">
    <div class="abs hero-image" role="img" aria-label="Desktop tower computer with flat monitor, keyboard and mouse"></div>
    <div class="abs hero-tag">Your No.1 Online Computer Systems and Components Retailer</div>
    <div class="abs hero-title">All Prices include GST, &amp; Free Delivery</div>
    <div class="abs hero-rule" style="left:336px;width:144px"></div>
    <div class="abs hero-rule" style="left:640px;width:170px"></div>
    <div class="abs hero-dots"><span></span><span class="on"></span><span></span><span></span><span></span></div>
  </div>
</section>

<section class="abs welcome">
  <h1>Welcome to <span>Quartz PCs</span></h1>
  <p>Sed ut perspiciatis unde omnis iste natus error sit voluptatem accusantium doloremque laudantium, totam rem aperiam, eaque ipsa quae ab illo inventore veritatis et quasi architecto beatae vitae dicta sunt explicabo. Nemo enim ipsam voluptatem quia voluptas sit aspernatur aut odit aut fugit, sed quia consequuntur magni dolores eos qui ratione voluptatem sequi nesciunt. Neque porro quisquam est, qui dolorem ipsum quia dolor sit amet, consectetur, adipisci velit, sed quia non numquam eius modi tempora incidunt ut labore et dolore magnam.</p>
</section>

<section class="abs panel" style="top:621px">
  <div class="panel-head"><h2>Current Specials</h2><a href="#">View all</a></div>
  <div class="products">
    <div class="product"><div class="product-img" role="img" aria-label="GPS navigation unit" style="background:linear-gradient(#3a3a3a,#5b7a4a)"></div><div class="price">$167.00</div><div class="warranty">Warranty:12 Months</div><div class="add-btn">🛒 ADD TO CART</div></div>
    <div class="product"><div class="product-img" role="img" aria-label="Universal remote control" style="width:14px;background:linear-gradient(#888,#444)"></div><div class="price">$167.00</div><div class="warranty">Warranty:12 Months</div><div class="add-btn">🛒 ADD TO CART</div></div>
    <div class="product"><div class="product-img" role="img" aria-label="Wireless router" style="background:linear-gradient(#fff 40%,#2a4c9a 41%,#1b2f60)"></div><div class="price">$167.00</div><div class="warranty">Warranty:12 Months</div><div class="add-btn">🛒 ADD TO CART</div></div>
    <div class="product"><div class="product-img" role="img" aria-label="Graphics card" style="background:linear-gradient(135deg,#2a5ea8,#1c1c1c)"></div><div class="price">$167.00</div><div class="warranty">Warranty:12 Months</div><div class="add-btn">🛒 ADD TO CART</div></div>
    <div class="product"><div class="product-img" role="img" aria-label="Power supply unit" style="background:linear-gradient(135deg,#555,#222)"></div><div class="price">$167.00</div><div class="warranty">Warranty:12 Months</div><div class="add-btn">🛒 ADD TO CART</div></div>
  </div>
</section>

<section class="abs panel" style="top:825px">
  <div class="panel-head"><h2>Whats New</h2><a href="#">View all</a></div>
  <div class="products">
    <div class="product"><div class="product-img" role="img" aria-label="Solid state drive" style="background:linear-gradient(135deg,#111,#333)"></div><div class="price">$167.00</div><div class="warranty">Warranty:12 Months</div><div class="add-btn">🛒 ADD TO CART</div></div>
    <div class="product"><div class="product-img" role="img" aria-label="Modular power supply" style="width:42px;background:linear-gradient(135deg,#666,#222)"></div><div class="price">$167.00</div><div class="warranty">Warranty:12 Months</div><div class="add-btn">🛒 ADD TO CART</div></div>
    <div class="product"><div class="product-img" role="img" aria-label="Internal drive enclosure" style="width:34px;background:linear-gradient(#3a3a3a,#111)"></div><div class="price">$167.00</div><div class="warranty">Warranty:12 Months</div><div class="add-btn">🛒 ADD TO CART</div></div>
    <div class="product"><div class="product-img" role="img" aria-label="Gaming mouse" style="border-radius:50%;background:linear-gradient(135deg,#e8541a,#1a1a1a)"></div><div class="price">$167.00</div><div class="warranty">Warranty:12 Months</div><div class="add-btn">🛒 ADD TO CART</div></div>
    <div class="product"><div class="product-img" role="img" aria-label="Power supply unit" style="background:linear-gradient(135deg,#555,#222)"></div><div class="price">$167.00</div><div class="warranty">Warranty:12 Months</div><div class="add-btn">🛒 ADD TO CART</div></div>
  </div>
</section>

<aside class="abs cats">
  <ul>
    <li>Accessories</li><li>Add-On Cards</li><li>Barebones Systems</li><li>Blu-Ray Drives</li>
    <li>Bundles (CPU+Ram+Mobo)</li><li>Cables</li><li>Cases</li><li>CD Drives</li>
    <li>Computer Systems</li><li>Consumables</li><li>Cooling Accessories</li><li>CPUs</li>
    <li>Digital Cameras</li><li>Disk Drives</li><li>Drawing Tablets</li><li>DVD/DivX/Media Players</li>
    <li>DVD Drives</li><li>Enclosures</li><li>Fax Machines</li><li>Game Controllers</li><li>GPS Navigation</li>
  </ul>
</aside>

<footer class="abs footer">
  <div class="foot-head" style="left:0;width:233px;padding-left:24px;gap:10px;font-size:13.5px">
    <svg width="22" height="15" viewBox="0 0 22 15" aria-hidden="true"><rect x=".5" y=".5" width="21" height="14" fill="#dfe6f3" stroke="#9aa"/><path d="M.5.5 11 9 21.5.5" fill="none" stroke="#9aa"/></svg>
    Mailing List
  </div>
  <div class="foot-head" style="left:234px;width:284px;padding-left:14px;font-size:13.5px">Important Links</div>
  <div class="foot-head" style="left:519px;width:355px;padding-left:26px" ><span class="copyright">Copyright © 2012 www.qvz.co.nz &nbsp;All rights reserved</span></div>
  <div class="foot-col-line" style="left:233px"></div>
  <div class="foot-col-line" style="left:518px"></div>

  <div class="abs mail-input">Enter your mail ID</div>
  <div class="abs submit">SUBMIT</div>
  <div class="abs nz-fern" role="img" aria-label="Silver fern emblem"></div>
  <div class="abs nz-text">100% NZ OWNED<br>&amp; OPERATED</div>

  <div class="abs links" style="left:247px;top:40px">Contact Us<br>Feedback<br>How to Order<br>View your Order Status<br>Methods of Payment<br>How to make Payment</div>
  <div class="abs links" style="left:379px;top:40px">Returns &amp; Refunds<br>Manual Order Form<br>Return Authorisation Form</div>

  <div class="abs pay-row" style="left:587px;top:70px">Payments :
    <span class="pay">Paynet</span><span class="pay">CardOne</span><span class="pay">Maxi</span><span class="pay">CheckGo</span><span class="pay">Vesta</span>
  </div>
  <div class="abs social-row" style="left:558px;top:116px">Connect with us :
    <span class="social"><i></i>Friendly</span><span class="social"><i></i>Chirp</span><span class="social"><i></i>Searchly</span><span class="social"><i></i>Yodel</span>
  </div>
</footer>

</body>
</html>
```